Business Cards for IT Consulting Company (Managed Service Provider)

I am looking to have some business cards printed and would like some designs. We are an IT Consulting company based in Vancouver BC. I would like a nice clean and modern look to the cards. I have uploaded all the versions of my logo so parts can be used as needed. Here is a snippit from our website homepage:

Quillbrook Networks Ltd. is an IT Solutions Partner located in Vancouver BC, Canada. We offer IT solutions and support to customers in the greater Vancouver Area. With expertise in Microsoft platforms, as well as Linux and Mac OSX and over 12 years experience in the IT industry, Quillbrook Networks is dedicated to offering our clients top quality service and products. We take pride in the solutions we offer our customers. The greatest compliment a client can give us is to recommend our services.

Quillbrook Networks Ltd. offers a wide range of IT services from onsite service to remote support and managed service solutions. This allows clients to choose the support path that best suits their company’s needs. Supporting many different sized companies from small to enterprise level over the past 12 years Quillbrook Networks has the experience and expertise needed to ensure things run smoothly. Allowing our clients to focus on doing business.

Revolutionizing the way IT services are delivered.

Quillbrook Networks is dedicated to providing our clients with IT solutions that work and grow with them for years to come. This philosophy helps save money in the long run instead of replacing equipment constantly. Far too often IT solutions are not well thought out and while possibly solving the problem at hand, require replacement due to growth or quality within a very short time frame. Quillbrook Networks takes pride in providing solutions that will last and be able to accommodate growth without the need for replacement.

Industry/Entity Type

Information Technology

Contact Information for Business Card

Quillbrook Networks Ltd.
(Employee Name)
Eml: (Employees Email Address)
Web: quillbrook.me
Ph: 604-555-0148

Font styles to use
Serif
Sans Serif

Requirements
Must have
• The Company logo and company colors.
Nice to have
• - Our tag line: "Revolutionizing IT Services" or "Revolutionizing the way IT services are delivered."
• - Also I really like the idea of nature and technology together blending which is sort of where my logo came from so integrating that somehow onto the business cards would be great.

```html
<!DOCTYPE html>
<html lang="en">
<head>
<meta charset="UTF-8">
<title>Quillbrook Networks Business Cards</title>
<link rel="stylesheet" href="https://fonts.googleapis.com/css2?family=Montserrat:wght@400;500;600;700&display=swap">
<style>
  :root {
    --page-bg: #2b2b2b;
    --card-bg: #050505;
    --brand-blue: #1aa3e8;
    --ink-white: #ffffff;
    --ink-soft: #e6e6e6;
  }
  * { margin: 0; padding: 0; box-sizing: border-box; }
  html, body { width: 1200px; height: 900px; overflow: hidden; }
  body {
    background: var(--page-bg);
    font-family: "Montserrat", Arial, sans-serif;
    position: relative;
  }
  .card {
    position: absolute;
    left: 280px;
    width: 640px;
    height: 366px;
    background: var(--card-bg);
    overflow: hidden;
    box-shadow: 0 14px 30px rgba(0,0,0,0.45);
  }
  .card--back { top: 62px; }
  .card--front { top: 472px; }

  /* back */
  .tagline {
    position: absolute;
    left: 0; right: 0; top: 168px;
    text-align: center;
    color: var(--ink-white);
    font-size: 19px;
    font-weight: 500;
    letter-spacing: 1px;
  }
  .back-web {
    position: absolute;
    right: 40px; bottom: 34px;
    color: var(--ink-white);
    font-size: 13px;
    font-weight: 600;
    letter-spacing: 0.5px;
  }
  .back-web .accent { color: var(--brand-blue); }

  /* front */
  .corner-fill {
    position: absolute;
    right: 0; top: 0;
    width: 200px; height: 366px;
    background: var(--ink-white);
    clip-path: polygon(100% 30%, 100% 78%, 40% 78%);
  }
  .brand {
    position: absolute;
    left: 40px; top: 92px;
    display: flex;
    align-items: center;
    gap: 14px;
  }
  .brand-square {
    width: 26px; height: 26px;
    background: var(--brand-blue);
  }
  .brand-name {
    color: var(--brand-blue);
    font-size: 34px;
    font-weight: 600;
    line-height: 1;
    letter-spacing: 0.5px;
  }
  .person {
    position: absolute;
    left: 40px; top: 178px;
  }
  .person-name {
    color: var(--brand-blue);
    font-size: 21px;
    font-weight: 700;
    letter-spacing: 1.5px;
    text-transform: uppercase;
  }
  .person-role {
    color: var(--ink-white);
    font-size: 13px;
    font-weight: 600;
    letter-spacing: 1px;
    margin-top: 4px;
    text-transform: uppercase;
  }
  .edge-mark {
    position: absolute;
    left: 0; top: 258px;
    width: 30px; height: 14px;
    display: flex;
  }
  .edge-mark span { flex: 1; }
  .edge-mark .white { background: var(--ink-white); }
  .edge-mark .blue { background: var(--brand-blue); }
  .contact-list {
    position: absolute;
    left: 58px; top: 240px;
    list-style: none;
  }
  .contact-list li {
    display: flex;
    align-items: center;
    gap: 10px;
    color: var(--ink-soft);
    font-size: 14px;
    font-weight: 600;
    letter-spacing: 0.5px;
    margin-bottom: 8px;
  }
  .contact-list svg { width: 12px; height: 12px; flex: none; }
</style>
</head>
<body>

  <section class="card card--back" aria-label="Card back">
    <p class="tagline">Revolutionizing IT Services</p>
    <p class="back-web">www.<span class="accent">quillbrook</span>.me</p>
  </section>

  <section class="card card--front" aria-label="Card front">
    <div class="corner-fill"></div>

    <div class="brand">
      <span class="brand-square"></span>
      <span class="brand-name">Quillbrook Networks Ltd.</span>
    </div>

    <div class="person">
      <p class="person-name">Marcus Ellery</p>
      <p class="person-role">Director</p>
    </div>

    <div class="edge-mark"><span class="white"></span><span class="blue"></span></div>

    <ul class="contact-list">
      <li>
        <svg viewBox="0 0 24 24" aria-hidden="true"><path fill="#1aa3e8" d="M6.6 10.8a15.1 15.1 0 0 0 6.6 6.6l2.2-2.2c.3-.3.7-.4 1-.2 1.1.4 2.3.6 3.6.6.6 0 1 .4 1 1V20c0 .6-.4 1-1 1A17 17 0 0 1 3 4c0-.6.4-1 1-1h3.5c.6 0 1 .4 1 1 0 1.3.2 2.5.6 3.6.1.3 0 .7-.2 1z"/></svg>
        604-555-0148
      </li>
      <li>
        <svg viewBox="0 0 24 24" aria-hidden="true"><rect x="2" y="5" width="20" height="14" fill="none" stroke="#1aa3e8" stroke-width="2"/><path d="M2 5l10 8 10-8" fill="none" stroke="#1aa3e8" stroke-width="2"/></svg>
        info@marcusellery.com
      </li>
      <li>
        <svg viewBox="0 0 24 24" aria-hidden="true"><circle cx="12" cy="12" r="10" fill="none" stroke="#1aa3e8" stroke-width="2"/><path d="M2 12h20M12 2c3 3 3 17 0 20M12 2c-3 3-3 17 0 20" fill="none" stroke="#1aa3e8" stroke-width="2"/></svg>
        www.quillbrook.me
      </li>
    </ul>
  </section>

</body>
</html>
```